Business Card Design for BrightvaleMedia.com

--I need a business card design for my company BrightvaleMedia.com

I have attached my logo...I want the brightvale media logo on the front of the business card, and then I want The Quillstone Chief on the back of it with my information.

I would like to see a light colored background as well as a dark colored background

FRONT:
BRIGHTVALE MEDIA LOGO
248 N. Larkmoor
3rd Floor
San Diego CA 92173
www.BrightvaleMedia.com

Advanced Website & App Development
Websites, Apps, Online Voucher Systems

Leading Edge Marketing Services
SMS, VB, SMM, SEM,

BACK:
QUILLSTONE CHIEF LOGO
Dorian Pelletta
The Quillstone Chief
Call Or Text: 619-555-0148
Dorian@QuillstoneChief.example
www.QuillstoneChief.example

Target Market(s)

small business owners

Industry/Entity Type

Business Consultant

Contact Information for Business Card

FRONT:
BRIGHTVALE MEDIA LOGO
248 N. Larkmoor
3rd Floor
San Diego CA 92173
www.BrightvaleMedia.com

SMS, VB, SMM, SEM,

BACK:
QUILLSTONE CHIEF LOGO
Dorian Pelletta
The Quillstone Chief
Dorian@QuillstoneChief.example
www.QuillstoneChief.example

Requirements
Must have
• add this quote on it somewhere, anywhere,preferrably on back
• "The Fastest Way To Success Is To Take Action”
• — Dorian Pelletta, Quillstone Chief
Nice to have
• open
Should not have
• red

```html
<!DOCTYPE html>
<html lang="en">
<head>
<meta charset="utf-8">
<title>Brightvale Media – Business Card</title>
<link rel="stylesheet" href="https://fonts.googleapis.com/css2?family=Open+Sans:wght@400;600;700&display=swap">
<style>
  :root {
    --backdrop: #3b3531;
    --card: #0d0d0e;
    --brand-blue: #2a8fd0;
    --rule-grey: #8a8d91;
    --ink-white: #f2f2f2;
    --ink-soft: #d6d6d6;
    --ink-muted: #a9abae;
  }
  * { box-sizing: border-box; margin: 0; padding: 0; }
  html, body {
    width: 1200px; height: 900px; overflow: hidden;
    background: var(--backdrop);
    font-family: "Open Sans", Arial, sans-serif;
  }
  .card-set {
    position: absolute; inset: 0;
    display: flex; align-items: center; justify-content: center; gap: 50px;
  }
  .card {
    position: relative;
    width: 525px; height: 300px;
    background: var(--card);
    border-radius: 3px;
    box-shadow: 0 10px 30px rgba(0,0,0,.45);
    color: var(--ink-white);
    overflow: hidden;
  }

  /* Back: personal side */
  .card--personal .wordmark {
    position: absolute; left: 34px; top: 128px;
    font-size: 20px; font-weight: 600; letter-spacing: 1.5px;
    text-transform: uppercase; color: var(--brand-blue);
    white-space: nowrap;
  }
  .card--personal .divider {
    position: absolute; left: 266px; top: 60px; width: 1px; height: 160px;
    background: var(--brand-blue);
  }
  .card--personal .details {
    position: absolute; left: 282px; top: 68px;
  }
  .person-name { font-size: 17px; font-weight: 600; color: var(--brand-blue); line-height: 1.2; }
  .person-title { font-size: 13px; color: var(--ink-white); margin-top: 2px; }
  .contact-list { list-style: none; margin-top: 22px; }
  .contact-list li {
    display: flex; align-items: center; gap: 8px;
    font-size: 12px; line-height: 1.65; color: var(--ink-white);
    white-space: nowrap;
  }
  .contact-list svg { width: 10px; height: 10px; fill: var(--brand-blue); flex: none; }
  .quote {
    position: absolute; left: 0; right: 0; bottom: 22px;
    text-align: center; font-size: 11px; line-height: 1.45; color: var(--ink-soft);
  }
  .quote cite { font-style: normal; color: var(--ink-muted); }

  /* Front: company side */
  .card--company { text-align: center; }
  .card--company .wordmark {
    position: absolute; left: 0; right: 0; top: 44px;
    font-size: 30px; font-weight: 600; letter-spacing: 3px;
    color: var(--brand-blue);
  }
  .card--company .brand-rule {
    position: absolute; left: 105px; right: 105px; top: 92px;
    height: 1px; background: var(--rule-grey);
  }
  .card--company .info { position: absolute; left: 0; right: 0; top: 112px; }
  .address { font-size: 12.5px; line-height: 1.4; color: var(--ink-white); }
  .site { font-size: 12.5px; color: var(--ink-soft); }
  .site .domain { color: var(--brand-blue); }
  .offer { margin-top: 12px; font-size: 12.5px; font-weight: 700; line-height: 1.4; }
  .services { margin-top: 12px; font-size: 12.5px; line-height: 1.4; color: var(--ink-white); }
</style>
</head>
<body>
<main class="card-set">
  <section class="card card--personal" aria-label="Card back">
    <div class="wordmark">Quillstone Chief</div>
    <div class="divider"></div>
    <div class="details">
      <p class="person-name">Dorian Pelletta</p>
      <p class="person-title">The Quillstone Chief</p>
      <ul class="contact-list">
        <li>
          <svg viewBox="0 0 10 10" aria-hidden="true"><path d="M2.2 0.5l1.6 2-1 1c.6 1.3 1.5 2.2 2.8 2.8l1-1 2 1.6-.9 1.6C4 8.3 1.7 6 .5 1.4z"/></svg>
          619-555-0148
        </li>
        <li>
          <svg viewBox="0 0 10 10" aria-hidden="true"><path d="M0 2h10v6H0z M0 2l5 3.5L10 2" stroke="#0d0d0e" stroke-width=".8"/></svg>
          Dorian@QuillstoneChief.example
        </li>
        <li>
          <svg viewBox="0 0 10 10" aria-hidden="true"><circle cx="5" cy="5" r="5"/><path d="M0 5h10M5 0c-2 3-2 7 0 10M5 0c2 3 2 7 0 10" stroke="#0d0d0e" stroke-width=".7" fill="none"/></svg>
          www.QuillstoneChief.example
        </li>
      </ul>
    </div>
    <blockquote class="quote">
      “The Fastest Way To Success Is To Take Action”<br>
      <cite>— Dorian Pelletta, Quillstone Chief</cite>
    </blockquote>
  </section>

  <section class="card card--company" aria-label="Card front">
    <div class="wordmark">BRIGHTVALE MEDIA</div>
    <div class="brand-rule"></div>
    <div class="info">
      <p class="address">248 N. Larkmoor<br>3rd Floor, San Diego CA 92173</p>
      <p class="site">www.<span class="domain">BrightvaleMedia</span>.com</p>
      <p class="offer">Advanced Website &amp; App Development<br>Websites, Apps, Online Voucher Systems</p>
      <p class="services">Leading Edge Marketing Services<br>SMS | VB | SMM | SEM,</p>
    </div>
  </section>
</main>
</body>
</html>
```